BWP Business Card

A double sided business card based on your "Brindlewood Partners Ltd" Logo. To use the "BWP" logo on 1 side and the full company logo on the reverse.

Detials to be included:

Name: Tomas Wheeler
Postion: Consultant Orthotist & Expert Witness
T: +44 (0) 7700 938271
F: +44 (0) 7654 8820

```html
<!DOCTYPE html>
<html lang="en">
<head>
<meta charset="utf-8">
<title>Brindlewood Partners Ltd – Business Card</title>
<link rel="stylesheet" href="https://fonts.googleapis.com/css2?family=Cinzel:wght@500;600&family=Tinos:ital,wght@0,400;0,700;1,400&display=swap">
<style>
  :root {
    --navy: #1b3f73;
    --grey: #9a9a9a;
    --grey-light: #c9c9c9;
    --ink: #555;
    --paper: #ffffff;
    --backdrop: #e9e8e5;
  }
  * { box-sizing: border-box; margin: 0; padding: 0; }
  html, body { width: 1200px; height: 720px; overflow: hidden; }
  body {
    background: var(--backdrop);
    font-family: "Tinos", "Times New Roman", serif;
    position: relative;
  }
  .card {
    position: absolute;
    top: 205px;
    width: 540px;
    height: 309px;
    background: var(--paper);
    box-shadow: 0 2px 10px rgba(0,0,0,0.12);
    overflow: hidden;
  }
  .card--front { left: 40px; }
  .card--back { left: 620px; }

  /* Front: brand block */
  .brand-mark {
    position: absolute; left: 70px; top: 58px;
    display: flex; align-items: center; gap: 8px;
  }
  .brand-mark__square { width: 22px; height: 22px; background: var(--navy); }
  .brand-mark__name {
    font-family: "Cinzel", "Times New Roman", serif;
    font-weight: 600; font-size: 30px; color: var(--navy); letter-spacing: 2px;
  }
  .brand-divider {
    position: absolute; left: 222px; top: 40px; width: 1px; height: 76px;
    background: var(--grey-light);
  }
  .company {
    position: absolute; left: 236px; top: 38px;
  }
  .company__name {
    font-family: "Cinzel", "Times New Roman", serif;
    font-weight: 600; font-size: 24px; line-height: 26px; color: var(--navy);
  }
  .company__tagline {
    margin-top: 6px; padding-top: 3px;
    border-top: 1px solid var(--navy);
    font-family: "Cinzel", "Times New Roman", serif;
    font-size: 8.5px; font-weight: 500; letter-spacing: 0.6px; color: var(--navy);
  }
  .band-top {
    position: absolute; left: 0; top: 126px; width: 100%; height: 14px;
    background: var(--navy);
    border-top: 3px solid var(--grey-light);
  }
  .band-name {
    position: absolute; left: 0; top: 196px; width: 100%; height: 26px;
    background: var(--navy);
    border-top: 2px solid var(--grey-light);
    color: var(--paper);
    font-size: 14px; line-height: 24px; padding-left: 100px;
  }
  .band-name__person { font-weight: 700; font-size: 15px; }

  .details {
    position: absolute; left: 0; top: 234px; width: 100%;
    display: flex; font-size: 12.5px; color: var(--ink); line-height: 17px;
  }
  .details__address { width: 180px; text-align: right; padding: 10px 14px 0 0; }
  .details__rule { width: 1px; height: 58px; background: var(--grey-light); }
  .details__contacts { list-style: none; padding-left: 12px; }
  .details__contacts li { display: flex; align-items: center; gap: 6px; }
  .details__contacts svg { width: 11px; height: 11px; fill: var(--ink); }

  /* Back */
  .back-mark {
    position: absolute; inset: 0;
    display: flex; align-items: center; justify-content: center; gap: 22px;
  }
  .back-mark__square { width: 70px; height: 70px; background: var(--navy); }
  .back-mark__name {
    font-family: "Cinzel", "Times New Roman", serif;
    font-weight: 600; font-size: 88px; color: var(--navy); letter-spacing: 6px;
  }
</style>
</head>
<body>
  <section class="card card--front" aria-label="Business card front">
    <div class="brand-mark">
      <span class="brand-mark__square"></span>
      <span class="brand-mark__name">BWP</span>
    </div>
    <div class="brand-divider"></div>
    <div class="company">
      <p class="company__name">Brindlewood<br>Partners Ltd</p>
      <p class="company__tagline">Excellence in Medical Legal Reporting</p>
    </div>
    <div class="band-top"></div>
    <div class="band-name">
      <span class="band-name__person">Tomas Wheeler,</span> Consultant Orthotist &amp; Expert Witness
    </div>
    <div class="details">
      <p class="details__address">18 Halden Road Kingsbury<br>Surrey, KT4 2RN</p>
      <span class="details__rule"></span>
      <ul class="details__contacts">
        <li>
          <svg viewBox="0 0 12 12" aria-hidden="true"><path d="M2.5 1l2 2.4-1 1.2c.6 1.4 1.6 2.4 3 3l1.2-1L10 8.5 9 11C4.5 10.6 1.4 7.5 1 3z"/></svg>
          +44 (0) 7700 938271
        </li>
        <li>
          <svg viewBox="0 0 12 12" aria-hidden="true"><rect x="3" y="1" width="6" height="3"/><rect x="1" y="4.5" width="10" height="5" rx="1"/><rect x="3" y="8" width="6" height="3" fill="#fff" stroke="#555" stroke-width="0.8"/></svg>
          +44 (0) 7654 8820
        </li>
        <li>
          <svg viewBox="0 0 12 12" aria-hidden="true"><path d="M1 3h10v6.5H1z"/><path d="M1 3l5 3.6L11 3" stroke="#fff" stroke-width="0.9" fill="none"/></svg>
          tomas@brindlewoodpartners.co.uk
        </li>
      </ul>
    </div>
  </section>

  <section class="card card--back" aria-label="Business card back">
    <div class="back-mark">
      <span class="back-mark__square"></span>
      <span class="back-mark__name">BWP</span>
    </div>
  </section>
</body>
</html>
```